Brookvale Estates LLC stationary for a real estate property management company.

Create stationary (letterhead, envelopes, business cards) using Brookvale Estates LLC logo as primary creative element. Stationary design needs to be horizontal, leaving as much space as possible for correspondence copy. See attached Creative Brief and past stationary files for details.

Target Market(s)

Prospective apartment residents and current residents, vendors, and government agencies.

Industry/Entity Type

Property Management

Contact Information for Business Card

Business card employee title: Property Manager. Should include address, phone, fax, email, website, slogan, and Brookvale Estates logo.

Font styles to use
Sans Serif

Colors
0592cd
000000

Requirements
Must have
• Tone should be conservative, institutional, business (i.e. banking, finance, real estate). Must include: address, phone, fax, website, and slogan (see attached Creative Brief). Should be a horizontal design, leaving as much room as possible for letter correspondence copy.
Nice to have
• Please use an Arial or Helvetica style font.
Should not have
• Letterhead layout should leave as much room as possible for copy.

```html
<!DOCTYPE html>
<html lang="en">
<head>
<meta charset="utf-8">
<title>Brookvale Estates LLC – Business Card</title>
<link href="https://fonts.googleapis.com/css2?family=Arimo:wght@400;700&display=swap" rel="stylesheet">
<style>
  :root {
    --backdrop: #2a2a2c;
    --brand-blue: #0a6eaa;
    --brand-blue-light: #1796cf;
    --accent-blue: #0592cd;
    --band-grey: #4d4d50;
    --card-white: #f4f4f4;
    --back-grey-light: #737377;
    --back-grey-dark: #464648;
    --ink-white: #ffffff;
  }
  * { margin: 0; padding: 0; box-sizing: border-box; }
  html, body {
    width: 1200px; height: 960px; overflow: hidden;
    background: var(--backdrop);
    font-family: "Arimo", Arial, Helvetica, sans-serif;
  }
  .card {
    position: absolute;
    width: 600px; height: 343px;
    overflow: hidden;
    box-shadow: 0 3px 8px rgba(0,0,0,.5);
  }
  .card--front { left: 302px; top: 128px; background: var(--card-white); }
  .card--back {
    left: 299px; top: 488px; height: 342px;
    background: linear-gradient(135deg, var(--back-grey-light) 0%, var(--back-grey-dark) 55%, var(--back-grey-dark) 100%);
  }
  .card__waves { position: absolute; inset: 0; }

  .brand-mark {
    position: absolute; left: 44px; top: 88px;
    display: flex; align-items: center; gap: 10px;
  }
  .brand-mark__square { width: 34px; height: 34px; background: var(--accent-blue); }
  .brand-mark__name {
    font-weight: 700; font-size: 25px; line-height: 1;
    color: var(--accent-blue); letter-spacing: .5px;
  }

  .contact {
    position: absolute; right: 28px; top: 156px;
    text-align: right; color: var(--ink-white);
  }
  .contact__name { font-weight: 700; font-size: 20px; line-height: 1; }
  .contact__title { font-size: 15px; margin-top: 6px; }
  .contact__address { font-size: 13.5px; line-height: 18px; margin-top: 9px; }
  .contact__lines { list-style: none; margin-top: 8px; font-size: 13.5px; line-height: 19px; }
  .contact__lines li { display: flex; justify-content: flex-end; align-items: center; gap: 9px; }
  .contact__lines svg { width: 13px; height: 13px; fill: var(--ink-white); }

  .back__name {
    position: absolute; left: 0; right: 0; top: 150px;
    display: flex; justify-content: center; align-items: center; gap: 14px;
  }
  .back__circle { width: 36px; height: 36px; border-radius: 50%; background: var(--ink-white); }
  .back__wordmark { font-weight: 700; font-size: 34px; color: var(--ink-white); }
  .back__slogan {
    position: absolute; left: 0; right: 0; top: 288px;
    text-align: center; font-weight: 700; font-size: 16.5px; color: var(--ink-white);
  }
</style>
</head>
<body>

<section class="card card--front">
  <svg class="card__waves" viewBox="0 0 600 343" aria-hidden="true">
    <defs>
      <linearGradient id="blueFill" x1="0" y1="1" x2="1" y2="0">
        <stop offset="0" stop-color="#1598d2"/>
        <stop offset=".45" stop-color="#0a6eaa"/>
        <stop offset="1" stop-color="#0b66a4"/>
      </linearGradient>
    </defs>
    <path d="M0,228 C50,260 100,274 150,272 C240,264 320,195 385,142 C445,92 515,60 600,62 L600,343 L0,343 Z" fill="var(--band-grey)"/>
    <path d="M0,257 C60,280 110,283 160,276 C250,258 330,196 390,146 C450,96 520,66 600,68 L600,343 L0,343 Z" fill="#ffffff"/>
    <path d="M0,261 C60,284 110,287 160,280 C250,262 330,200 390,150 C450,100 520,70 600,72 L600,343 L0,343 Z" fill="url(#blueFill)"/>
  </svg>

  <div class="brand-mark">
    <span class="brand-mark__square"></span>
    <span class="brand-mark__name">BROOKVALE ESTATES LLC</span>
  </div>

  <div class="contact">
    <p class="contact__name">DANIEL HARTLEY</p>
    <p class="contact__title">Property Manager</p>
    <p class="contact__address">2750 Linden Grove Road #B210<br>Carlton Falls, CA 95012</p>
    <ul class="contact__lines">
      <li>555-014-2278
        <svg viewBox="0 0 16 16"><path d="M3.5 1 L6 1 L7 5 L5.3 6.3 C6.3 8.4 7.6 9.7 9.7 10.7 L11 9 L15 10 L15 12.5 C15 13.9 13.9 15 12.5 15 C6.7 15 1 9.3 1 3.5 C1 2.1 2.1 1 3.5 1 Z"/></svg>
      </li>
      <li>555-018-7340
        <svg viewBox="0 0 16 16"><path d="M4 1 H12 V5 H4 Z M1 6 H15 V12 H12 V10 H4 V12 H1 Z M5 11 H11 V15 H5 Z"/></svg>
      </li>
      <li>daniel@brookvaleestates.us
        <svg viewBox="0 0 16 16"><path d="M1 3 H15 V4 L8 9 L1 4 Z M1 5.5 L8 10.5 L15 5.5 V13 H1 Z"/></svg>
      </li>
      <li>www.brookvaleestates.us
        <svg viewBox="0 0 16 16"><circle cx="8" cy="8" r="7"/><path d="M5 4 C7 4 8 6 7 7 C6 8 4 7 4 9 M10 10 C11 9 12 11 11 12" stroke="#0b66a4" stroke-width="1.4" fill="none"/></svg>
      </li>
    </ul>
  </div>
</section>

<section class="card card--back">
  <div class="back__name">
    <span class="back__circle"></span>
    <span class="back__wordmark">Brookvale Estates</span>
  </div>
  <p class="back__slogan">Multifamily Property Management</p>
</section>

</body>
</html>
```